Bright Path Mentors Needs A New Website Design

We need a 8 page website designed for "Bright Path Mentors .ca" similar in design to: "keystone learning hub .com".

The winner/successful candidate on the home page will be asked to complete the following inner pages to complete the project:

About Us
Philosophy
How We Work
Work With Us
Blog
Find A Tutor
Contact

Target Market(s)

Tutoring business clients/children

Industry/Entity Type

Education

Number of Pages Required

5+ page

Font styles to use
Sans Serif

Requirements
Must have
• The attached logo included of course. Similar design to the design provided above in the brief. Clear high quality high resolution images of children in school settings.

```html
<!DOCTYPE html>
<html lang="en">
<head>
<meta charset="utf-8">
<title>Bright Path Mentors — How We Work</title>
<link href="https://fonts.googleapis.com/css2?family=Roboto+Slab:wght@400;700&family=Raleway:wght@400;500&family=Roboto:wght@400;500&family=Ubuntu:wght@400;500&display=swap" rel="stylesheet">
<style>
:root{
  --blue:#2e3192;
  --orange:#f7931e;
  --orange-light:#fdbe6d;
  --grey-band:#ededee;
  --text:#666;
  --dark:#1b1b1b;
  --white:#fff;
}
*{box-sizing:border-box;margin:0;padding:0}
html,body{width:871px;height:1200px;overflow:hidden;background:#fff}
body{position:relative;font-family:'Raleway',sans-serif;color:var(--text)}
.abs{position:absolute}

/* top bar */
.topbar{left:0;top:0;width:871px;height:34px;background:var(--orange-light)}
.promo{left:304px;top:9px;font:500 13.5px 'Roboto',sans-serif;color:#222;white-space:nowrap}
.social{display:flex;gap:5px}
.social span{width:24px;height:24px;border-radius:50%;display:flex;align-items:center;justify-content:center}
.top-social{left:640px;top:5px}
.top-social span{border:1.6px solid #222}
.free-tab{left:789px;top:0;width:82px;height:66px;z-index:3}
.free-tab span{position:absolute;left:0;top:6px;width:82px;text-align:center;font:400 12px/17px 'Roboto Slab',Georgia,serif;color:#fff;white-space:nowrap}

/* nav */
.navband{left:0;top:34px;width:871px;height:62px;background:var(--blue);border-bottom:2px solid var(--orange)}
.nav{left:243px;top:60px;display:flex;gap:13px;font:400 11px 'Roboto Slab',Georgia,serif;color:#fff;list-style:none;white-space:nowrap}
.logo-disc{left:72px;top:5px;width:124px;height:124px;border-radius:50%;background:#fff;display:flex;align-items:center;justify-content:center;text-align:center;z-index:2}
.logo-disc .name{font:700 13px/16px 'Roboto Slab',Georgia,serif;color:var(--blue);width:90px}

/* hero */
.hero{left:0;top:98px;width:871px;height:152px;background:linear-gradient(90deg,#8a7a68 0%,#b9a58c 45%,#c9b7a3 70%,#9a8f86 100%)}
.hero h1{position:absolute;left:70px;top:75px;font:700 34px 'Roboto Slab',Georgia,serif;color:#fff;letter-spacing:.5px}

/* sections */
.sec-title{font:400 21px 'Roboto Slab',Georgia,serif;color:var(--blue)}
.sec-title em{font-style:normal;color:var(--orange)}
.rule{height:2px;width:168px;background:var(--blue);margin-top:8px}
.copy p{font-size:9.2px;line-height:17.6px;margin-bottom:8.5px;color:#6d6d6d}
.s1{left:71px;top:284px;width:730px}
.s1 .copy{margin-top:14px}
.band{left:0;top:463px;width:871px;height:215px;background:var(--grey-band)}
.services{left:72px;top:486px;list-style:none}
.services li{display:flex;align-items:center;gap:11px;height:30px;font:400 13.6px 'Roboto Slab',Georgia,serif;color:#333}
.band-logo{left:572px;top:492px;width:156px;height:160px;display:flex;flex-direction:column;align-items:center;justify-content:center;gap:10px}
.band-logo .mark{width:70px;height:70px;border-radius:50%;border:3px solid var(--blue)}
.band-logo .name{font:700 18px 'Roboto Slab',Georgia,serif;color:var(--blue);text-align:center}
.s2{left:71px;top:698px;width:730px}
.s2 .copy{margin-top:14px}

/* footer */
.footer{left:0;top:912px;width:871px;height:243px;background:var(--dark)}
.foot-logo{left:72px;top:966px;width:140px;height:140px;display:flex;flex-direction:column;align-items:center;justify-content:center;gap:10px}
.foot-logo .mark{width:70px;height:70px;border-radius:50%;border:3px solid #fff}
.foot-logo .name{font:700 16px 'Roboto Slab',Georgia,serif;color:#fff;text-align:center}
.fh{font:500 13px 'Ubuntu',sans-serif;color:#fff;letter-spacing:.3px}
.fh::after{content:"";display:block;width:76px;height:1.5px;background:#fff;margin-top:7px}
.links{left:270px;top:941px}
.links ul{list-style:none;margin-top:18px}
.links li{font:400 10.5px 'Ubuntu',sans-serif;color:#fff;height:23px}
.contact{left:411px;top:941px}
.c-row{display:flex;gap:12px;margin-top:16px}
.c-row:first-of-type{margin-top:18px}
.c-ico{width:29px;height:29px;border:1.5px solid #fff;border-radius:50%;display:flex;align-items:center;justify-content:center;flex:none}
.c-row b{display:block;font:500 11px 'Ubuntu',sans-serif;color:#fff;margin-bottom:4px}
.c-row span{font:400 9px/14px 'Ubuntu',sans-serif;color:#fff}
.work{left:590px;top:941px;width:208px}
.form{margin-top:18px;display:grid;grid-template-columns:1fr 1fr;gap:5px}
.field{border:1px solid #fff;border-radius:3px;height:26px;font:400 8px 'Ubuntu',sans-serif;color:#fff;padding:8px 8px;position:relative}
.field.full{grid-column:1/3}
.field.msg{height:48px}
.submit{margin-top:7px;width:86px;height:28px;background:var(--orange);color:#fff;font:500 8.5px 'Ubuntu',sans-serif;display:flex;align-items:center;justify-content:center;border-radius:2px}
.bottom{left:0;top:1155px;width:871px;height:45px;background:var(--orange)}
.copyright{left:71px;top:1171px;font:400 10px 'Ubuntu',sans-serif;color:#fff}
.pay{left:512px;top:1168px;display:flex;gap:4px;align-items:center}
.pay span{display:flex;align-items:center;justify-content:center;height:18px;padding:0 5px;background:#fff;border-radius:2px;font:500 8.5px 'Ubuntu',sans-serif;color:var(--blue)}
.bot-social{left:688px;top:1165px}
.bot-social span{border:1.6px solid #fff}
</style>
</head>
<body>

<div class="abs topbar"></div>
<div class="abs promo">"First Session Just $35 - Call 1-855-310-7624 Now"</div>
<div class="abs social top-social">
  <span><svg width="12" height="12" viewBox="0 0 12 12"><circle cx="3" cy="6" r="1.6" fill="#222"/><circle cx="9" cy="2.5" r="1.6" fill="#222"/><circle cx="9" cy="9.5" r="1.6" fill="#222"/><path d="M3 6 L9 2.5 M3 6 L9 9.5" stroke="#222" stroke-width="1"/></svg></span>
  <span><svg width="12" height="11" viewBox="0 0 12 11"><path d="M6 10 L1.3 5.4 A2.7 2.7 0 0 1 6 2 A2.7 2.7 0 0 1 10.7 5.4 Z" fill="#222"/></svg></span>
  <span><svg width="12" height="11" viewBox="0 0 12 11"><path d="M1 1 H11 V7 H5 L2.5 9.5 V7 H1 Z" fill="#222"/></svg></span>
  <span><svg width="12" height="12" viewBox="0 0 12 12"><path d="M6 .8 L7.5 4.4 L11.3 4.6 L8.4 7 L9.3 10.8 L6 8.7 L2.7 10.8 L3.6 7 L.7 4.6 L4.5 4.4 Z" fill="#222"/></svg></span>
  <span><svg width="12" height="9" viewBox="0 0 12 9"><rect x=".5" y=".5" width="11" height="8" rx="1" fill="#222"/><path d="M1 1 L6 5 L11 1" fill="none" stroke="#fdbe6d" stroke-width="1"/></svg></span>
</div>
<svg class="abs free-tab" viewBox="0 0 82 66"><polygon points="0,0 82,0 82,52 41,66 0,52" fill="#f7931e"/></svg>
<div class="abs free-tab"><span>Free<br>Assessment</span></div>

<div class="abs navband"></div>
<ul class="abs nav">
  <li>HOME</li><li>ABOUT US</li><li>PHILOSOPHY</li><li>HOW WE WORK</li><li>WORK WITH US</li><li>BLOG</li><li>FIND A TUTOR</li><li>CONTACT</li>
</ul>
<div class="abs logo-disc"><div class="name">Bright Path Mentors</div></div>

<div class="abs hero" role="img" aria-label="Photo of children raising their hands in a classroom">
  <h1>HOW WE WORK</h1>
</div>

<section class="abs s1">
  <h2 class="sec-title"><em>HOW</em> BRIGHT PATH MENTORS WORK</h2>
  <div class="rule"></div>
  <div class="copy">
    <p>At Bright Path Mentors we understand the importance of having the right tools when it comes to learning. Having a good tutor can be just that! Our tutors can truly transform your child's learning experience and give them the confidence they need to succeed!</p>
    <p>We only hire teachers as tutors, and our team of Ontario Certified Teachers (OCT) are passionate about education, offering some of the best teachers in the industry. We believe that tutoring ensures that your child is getting the instruction they need, as well as the tools and confidence to surpass their goals!</p>
    <p>Our teachers come to you. We work around your schedule to make tutoring as convenient as possible on those busy evenings and weekends!</p>
  </div>
</section>

<div class="abs band"></div>
<ul class="abs services">
  <li><svg width="24" height="18" viewBox="0 0 24 18"><path d="M1 6 L12 1 L23 6 L12 11 Z M5 8 V13 Q12 17 19 13 V8" fill="none" stroke="#2e3192" stroke-width="1.6"/></svg>Specific subject tutoring</li>
  <li><svg width="24" height="18" viewBox="0 0 24 18"><path d="M1 6 L12 1 L23 6 L12 11 Z M5 8 V13 Q12 17 19 13 V8" fill="none" stroke="#2e3192" stroke-width="1.6"/></svg>Work along side the Ontario Curriculum</li>
  <li><svg width="24" height="18" viewBox="0 0 24 18"><path d="M1 6 L12 1 L23 6 L12 11 Z M5 8 V13 Q12 17 19 13 V8" fill="none" stroke="#2e3192" stroke-width="1.6"/></svg>Test and exam preparation</li>
  <li><svg width="24" height="18" viewBox="0 0 24 18"><path d="M1 6 L12 1 L23 6 L12 11 Z M5 8 V13 Q12 17 19 13 V8" fill="none" stroke="#2e3192" stroke-width="1.6"/></svg>Remedial programs</li>
  <li><svg width="24" height="18" viewBox="0 0 24 18"><path d="M1 6 L12 1 L23 6 L12 11 Z M5 8 V13 Q12 17 19 13 V8" fill="none" stroke="#2e3192" stroke-width="1.6"/></svg>Assist with organization skills and study habits</li>
  <li><svg width="24" height="18" viewBox="0 0 24 18"><path d="M1 6 L12 1 L23 6 L12 11 Z M5 8 V13 Q12 17 19 13 V8" fill="none" stroke="#2e3192" stroke-width="1.6"/></svg>Subject enrichment programs</li>
</ul>
<div class="abs band-logo"><div class="mark"></div><div class="name">Bright Path Mentors</div></div>

<section class="abs s2">
  <h2 class="sec-title"><em>GREAT TUTORS</em> MAKE GREAT STUDENTS</h2>
  <div class="rule"></div>
  <div class="copy">
    <p>Furthermore our tutors will keep you up to date on each lesson. Progress is monitored through feedback that is given to parents on a weekly basis. Our tutors are keen on keeping parents in the loop. We believe that open communication with parents is critical to the overall success of a student!</p>
    <p>One-on-one tutoring is more than just having your child understand concepts; it is also about confidence boosting! Our tutors take the time to help your child learn in ways that are tailored to their learning style. When students learn in a way they can understand they feel good! Their confidence builds and they form that " I can do it!" attitude!</p>
    <p>Our goal is to approach teaching in a holistic way. Our tutors help students learn, study, think critically, and build their confidence all while providing a supportive and lively environment for them to ask questions and engage!</p>
  </div>
</section>

<footer>
  <div class="abs footer"></div>
  <div class="abs foot-logo"><div class="mark"></div><div class="name">Bright Path Mentors</div></div>

  <div class="abs links">
    <h3 class="fh">QUICK LINKS</h3>
    <ul>
      <li>›&nbsp; Home</li><li>›&nbsp; About Us</li><li>›&nbsp; Philosophy</li><li>›&nbsp; How We Work</li><li>›&nbsp; Work With Us</li><li>›&nbsp; Contact Us</li>
    </ul>
  </div>

  <div class="abs contact">
    <h3 class="fh">CONTACT US</h3>
    <div class="c-row">
      <div class="c-ico"><svg width="10" height="13" viewBox="0 0 10 13"><path d="M5 12 C2 8 1 6 1 4.5 A4 4 0 0 1 9 4.5 C9 6 8 8 5 12Z" fill="none" stroke="#fff" stroke-width="1.3"/><circle cx="5" cy="4.5" r="1.3" fill="#fff"/></svg></div>
      <div><b>BRIGHTPATHMENTORS,</b><span>2750 Maple Ave #210,<br>North York, ON M2N</span></div>
    </div>
    <div class="c-row">
      <div class="c-ico"><svg width="8" height="12" viewBox="0 0 8 12"><rect x="1" y="1" width="6" height="10" rx="1" fill="none" stroke="#fff" stroke-width="1.3"/></svg></div>
      <div><b>PHONE:</b><span>1-855-310-7624</span></div>
    </div>
    <div class="c-row">
      <div class="c-ico"><svg width="12" height="9" viewBox="0 0 12 9"><rect x="0.5" y="0.5" width="11" height="8" rx="1" fill="#fff"/><path d="M1 1 L6 5 L11 1" fill="none" stroke="#1b1b1b" stroke-width="1"/></svg></div>
      <div><b>Mail:</b><span>info@brightpathmentors.ca</span></div>
    </div>
  </div>

  <div class="abs work">
    <h3 class="fh">WORK WITH US</h3>
    <div class="form">
      <div class="field">Name</div>
      <div class="field">Phone</div>
      <div class="field full">Upload Resume
        <svg style="position:absolute;right:8px;top:7px" width="11" height="11" viewBox="0 0 11 11"><path d="M5.5 1 L2 4.5 H4 V7 H7 V4.5 H9 Z M1 8.5 H10 V10 H1 Z" fill="#fff"/></svg>
      </div>
      <div class="field full msg">Message</div>
    </div>
    <div class="submit">SUBMIT NOW</div>
  </div>

  <div class="abs bottom"></div>
  <div class="abs copyright">Copyright © 2016 Bright Path Mentors. All Right Reserved</div>
  <div class="abs pay">
    <span>PayEase</span><span>Nova</span><span>Zento</span><span>Orba</span>
  </div>
  <div class="abs social bot-social">
    <span><svg width="12" height="12" viewBox="0 0 12 12"><circle cx="3" cy="6" r="1.6" fill="#fff"/><circle cx="9" cy="2.5" r="1.6" fill="#fff"/><circle cx="9" cy="9.5" r="1.6" fill="#fff"/><path d="M3 6 L9 2.5 M3 6 L9 9.5" stroke="#fff" stroke-width="1"/></svg></span>
    <span><svg width="12" height="11" viewBox="0 0 12 11"><path d="M6 10 L1.3 5.4 A2.7 2.7 0 0 1 6 2 A2.7 2.7 0 0 1 10.7 5.4 Z" fill="#fff"/></svg></span>
    <span><svg width="12" height="11" viewBox="0 0 12 11"><path d="M1 1 H11 V7 H5 L2.5 9.5 V7 H1 Z" fill="#fff"/></svg></span>
    <span><svg width="12" height="12" viewBox="0 0 12 12"><path d="M6 .8 L7.5 4.4 L11.3 4.6 L8.4 7 L9.3 10.8 L6 8.7 L2.7 10.8 L3.6 7 L.7 4.6 L4.5 4.4 Z" fill="#fff"/></svg></span>
  </div>
</footer>

</body>
</html>
```